Automotive eCommerce Business looking for a business card design

Looking for a clean and simple business card design. Our company name is "Brindle Auto" and we are a company specializing in the ecommerce sales of automotive parts, specifically for pick up trucks and large SUVs. Our company colours are red, black, and white.

Feel free to use the logo provided or create a new logo that you seem fit. Looking forward to your creative ideas!

Industry/Entity Type

Automotive

Contact Information for Business Card

We were thinking of a possibly two-sided design featuring just the logo and company name on one side, and personal information on the other side. Single sided designs will be considered as well.

Font styles to use
Serif
Sans Serif
Decorative

Colors
ec1f27
ffffff
000000

Requirements
Must have
• Space for employee's name, title, phone number and email address, along with the company address and website somewhere.

```html
<!DOCTYPE html>
<html lang="en">
<head>
<meta charset="utf-8">
<title>Brindle Auto – Business Card</title>
<link href="https://fonts.googleapis.com/css2?family=Cinzel:wght@400;600&family=Roboto:wght@400&family=Roboto+Condensed:wght@400;700&display=swap" rel="stylesheet">
<style>
  :root {
    --brand-red: #a51e22;
    --brand-red-faint: #f1dcdd;
    --ink: #4a4a4a;
    --ink-soft: #555555;
    --band-grey: #50575c;
    --card-white: #f4f4f4;
    --backdrop: #e6e3df;
  }
  * { box-sizing: border-box; margin: 0; padding: 0; }
  html, body { width: 1200px; height: 960px; overflow: hidden; }
  body { background: var(--backdrop); position: relative; font-family: "Roboto", Arial, sans-serif; }

  .card {
    position: absolute;
    background: var(--card-white);
    border-radius: 18px;
    overflow: hidden;
    box-shadow: 0 3px 8px rgba(0,0,0,0.18);
  }

  /* Front side */
  .card-front { left: 318px; top: 95px; width: 602px; height: 355px; }
  .front-mark {
    position: absolute; left: 271px; top: 90px;
    width: 60px; height: 60px; background: var(--brand-red); border-radius: 6px;
  }
  .front-name {
    position: absolute; left: 0; right: 0; top: 243px;
    text-align: center;
    font-family: "Cinzel", Georgia, serif; font-weight: 600;
    font-size: 25px; letter-spacing: 0.5px; color: var(--ink);
  }
  .front-web {
    position: absolute; left: 0; right: 0; top: 304px;
    text-align: center; font-size: 14px; letter-spacing: 5.5px; color: var(--ink-soft);
  }

  /* Back side */
  .card-back { left: 320px; top: 492px; width: 600px; height: 343px; }
  .side-band { position: absolute; left: 0; top: 0; bottom: 0; width: 20px; background: var(--band-grey); }
  .side-tab {
    position: absolute; left: 0; top: 48px; width: 20px; height: 86px;
    background: var(--brand-red); border-radius: 0 10px 10px 0;
  }
  .back-faint-mark {
    position: absolute; left: 300px; top: 78px; width: 290px; height: 290px;
    background: var(--brand-red-faint); border-radius: 24px;
  }
  .back-logo { position: absolute; left: 40px; top: 40px; width: 120px; text-align: center; }
  .back-logo-square { width: 56px; height: 56px; background: var(--brand-red); border-radius: 6px; margin: 0 auto 10px; }
  .back-logo-name {
    font-family: "Roboto Condensed", "Arial Narrow", sans-serif; font-weight: 700;
    font-size: 17px; color: var(--brand-red); letter-spacing: 0.5px;
  }
  .person { position: absolute; left: 218px; top: 68px; font-family: "Roboto Condensed", "Arial Narrow", sans-serif; }
  .person-name { font-weight: 700; font-size: 21px; color: var(--brand-red); line-height: 1.1; }
  .person-title { font-size: 15.5px; color: var(--ink); margin-top: 4px; }

  .contacts { position: absolute; left: 218px; top: 169px; list-style: none; font-size: 14.5px; color: var(--ink); }
  .contacts li { display: flex; align-items: flex-start; line-height: 19px; }
  .contacts li.address { margin-bottom: 10px; }
  .contacts svg { width: 14px; height: 14px; margin: 2px 24px 0 0; fill: var(--brand-red); flex: none; }
</style>
</head>
<body>

<section class="card card-front" aria-label="Business card front">
  <div class="front-mark"></div>
  <h1 class="front-name">Brindle Auto Ltd.</h1>
  <p class="front-web">www.brindleauto.com</p>
</section>

<section class="card card-back" aria-label="Business card back">
  <div class="back-faint-mark"></div>
  <div class="side-band"></div>
  <div class="side-tab"></div>

  <div class="back-logo">
    <div class="back-logo-square"></div>
    <div class="back-logo-name">BRINDLE AUTO</div>
  </div>

  <div class="person">
    <h2 class="person-name">OWEN HARTLEY</h2>
    <p class="person-title">CEO/FOUNDER</p>
  </div>

  <ul class="contacts">
    <li class="address">
      <svg viewBox="0 0 14 14"><path d="M7 0a5 5 0 0 0-5 5c0 3.5 5 9 5 9s5-5.5 5-9a5 5 0 0 0-5-5zm0 7a2 2 0 1 1 0-4 2 2 0 0 1 0 4z"/></svg>
      <span>4120 Larkspur Road<br>Fairbanks, Alaska 99701</span>
    </li>
    <li>
      <svg viewBox="0 0 14 14"><path d="M3 0l3 3-1.6 2a8 8 0 0 0 4.6 4.6L11 8l3 3-2 2.5C6 13.5 .5 8 .5 2z"/></svg>
      <span>907 555 0142</span>
    </li>
    <li>
      <svg viewBox="0 0 14 14"><path d="M3.5 0h7a1 1 0 0 1 1 1v12a1 1 0 0 1-1 1h-7a1 1 0 0 1-1-1V1a1 1 0 0 1 1-1zm.8 1.5v9.5h5.4V1.5zM7 11.6a.8.8 0 1 0 0 1.6.8.8 0 0 0 0-1.6z"/></svg>
      <span>907 555 0187</span>
    </li>
    <li>
      <svg viewBox="0 0 14 14"><path d="M3 0h7l1 1v3H3zM0 5h14v6h-2v3H2v-3H0zm3.5 4v3.5h7V9z"/></svg>
      <span>907 555 0163</span>
    </li>
    <li>
      <svg viewBox="0 0 14 14"><path d="M0 2.5h14v1L7 8 0 3.5zM0 5l7 4.5L14 5v7H0z"/></svg>
      <span>owen@brindleauto.com</span>
    </li>
    <li>
      <svg viewBox="0 0 14 14"><path d="M7 0a7 7 0 1 0 0 14A7 7 0 0 0 7 0zm-1 2.5 2 1-1 2h-2l-1 2 2 2v2.5L3.5 9 2 6.5A5.5 5.5 0 0 1 6 2.5zm4 1.5a5.5 5.5 0 0 1 1.5 5L10 8 9 6z"/></svg>
      <span>www.brindleauto.com</span>
    </li>
  </ul>
</section>

</body>
</html>
```